professional business card design for technology company

We are a small technology consulting firm, specialising in consulting based around Cloud and Managed services. Our colour scheme is yellow, blue and white, as you can see in the logos. Although we are based in melbourne australia, due to the nature of our work, our clients can be located anywhere. We are looking for a clean, professional, positive look - similar to our company logo

Target Market(s)

small business

Industry/Entity Type

Business

Contact Information for Business Card

eye catching, designed to incorporate some level of raised printing. Must contain website address, phone number, name and job title

Requirements
Must have
• Logo (attached) - use of the same colour scheme

```html
<!DOCTYPE html>
<html lang="en">
<head>
<meta charset="utf-8">
<title>Nubrava Business Card</title>
<link rel="stylesheet" href="https://fonts.googleapis.com/css2?family=Questrial&family=Michroma&display=swap">
<style>
  :root {
    --backdrop: #e9eaec;
    --card-white: #ffffff;
    --card-shade: #f1f1f2;
    --slate: #5d5e60;
    --slate-dark: #4a4b4d;
    --sky: #3aa9e3;
    --ink: #3b3c3e;
    --contact-text: #ffffff;
  }
  * { margin: 0; padding: 0; box-sizing: border-box; }
  html, body {
    width: 1200px;
    height: 900px;
    overflow: hidden;
    background: var(--backdrop);
  }
  .canvas {
    position: relative;
    width: 1200px;
    height: 900px;
    display: flex;
    align-items: center;
    justify-content: center;
  }
  .business-card {
    position: relative;
    width: 900px;
    height: 514px;
    border-radius: 34px;
    overflow: hidden;
    background: linear-gradient(160deg, var(--card-white) 40%, var(--card-shade) 100%);
    box-shadow: 0 18px 40px rgba(0, 0, 0, 0.18);
  }
  .card-waves {
    position: absolute;
    inset: 0;
    width: 100%;
    height: 100%;
  }
  .brand {
    position: absolute;
    left: 470px;
    top: 150px;
    display: flex;
    align-items: center;
    gap: 16px;
  }
  .brand-dot {
    width: 26px;
    height: 26px;
    border-radius: 50%;
    background: var(--sky);
  }
  .brand-name {
    font-family: "Questrial", sans-serif;
    font-size: 92px;
    line-height: 1;
    color: var(--slate);
    letter-spacing: -1px;
  }
  .holder {
    position: absolute;
    left: 520px;
    top: 300px;
    text-align: center;
    width: 330px;
    color: var(--ink);
  }
  .holder-name {
    font-family: "Michroma", sans-serif;
    font-size: 19px;
    letter-spacing: 2px;
  }
  .holder-title {
    font-family: "Questrial", sans-serif;
    font-size: 20px;
    margin-top: 4px;
  }
  .contact-list {
    position: absolute;
    left: 24px;
    top: 252px;
    list-style: none;
    font-family: "Questrial", sans-serif;
    font-size: 13px;
    color: var(--contact-text);
  }
  .contact-item {
    display: flex;
    align-items: center;
    gap: 9px;
    height: 22px;
  }
  .contact-icon {
    width: 15px;
    height: 15px;
    flex: none;
  }
</style>
</head>
<body>
<main class="canvas">
  <article class="business-card">
    <svg class="card-waves" viewBox="0 0 900 514" preserveAspectRatio="none" aria-hidden="true">
      <path d="M0,42 C150,62 210,200 310,300 C400,390 580,420 900,340" fill="none" stroke="var(--sky)" stroke-width="3"/>
      <path d="M0,60 C150,80 215,215 315,318 C405,408 585,432 900,360 L900,514 L0,514 Z" fill="var(--sky)"/>
      <path d="M0,74 C150,94 210,232 305,336 C395,428 580,448 900,392 L900,514 L0,514 Z" fill="var(--slate)"/>
    </svg>

    <div class="brand">
      <span class="brand-dot"></span>
      <span class="brand-name">Nubrava</span>
    </div>

    <div class="holder">
      <p class="holder-name">TOBIAS RENWICK</p>
      <p class="holder-title">Managing Director</p>
    </div>

    <ul class="contact-list">
      <li class="contact-item">
        <svg class="contact-icon" viewBox="0 0 16 16"><circle cx="8" cy="8" r="8" fill="#fff"/><path d="M5.2 4.2l1.4-.3.8 1.9-.9.7c.5 1 1.2 1.7 2.2 2.2l.7-.9 1.9.8-.3 1.4c-3.2.1-5.9-2.6-5.8-5.8z" fill="var(--slate-dark)"/></svg>
        <span>014 552 3190</span>
      </li>
      <li class="contact-item">
        <svg class="contact-icon" viewBox="0 0 16 16"><circle cx="8" cy="8" r="8" fill="#fff"/><path d="M5.2 4.2l1.4-.3.8 1.9-.9.7c.5 1 1.2 1.7 2.2 2.2l.7-.9 1.9.8-.3 1.4c-3.2.1-5.9-2.6-5.8-5.8z" fill="var(--slate-dark)"/></svg>
        <span>014 552 3190</span>
      </li>
      <li class="contact-item">
        <svg class="contact-icon" viewBox="0 0 16 16"><circle cx="8" cy="8" r="8" fill="#fff"/><rect x="4" y="5.2" width="8" height="5.6" rx="0.6" fill="var(--slate-dark)"/><path d="M4.3 5.6L8 8.4l3.7-2.8" fill="none" stroke="#fff" stroke-width="0.8"/></svg>
        <span>hello@nubrava.com</span>
      </li>
      <li class="contact-item">
        <svg class="contact-icon" viewBox="0 0 16 16"><circle cx="8" cy="8" r="8" fill="#fff"/><circle cx="8" cy="8" r="4" fill="none" stroke="var(--slate-dark)" stroke-width="1"/><path d="M4 8h8M8 4c-1.6 2.4-1.6 5.6 0 8M8 4c1.6 2.4 1.6 5.6 0 8" fill="none" stroke="var(--slate-dark)" stroke-width="0.8"/></svg>
        <span>www.nubrava.com</span>
      </li>
      <li class="contact-item">
        <svg class="contact-icon" viewBox="0 0 16 16"><circle cx="8" cy="8" r="8" fill="#fff"/><path d="M8 3.6c-1.8 0-3 1.3-3 2.9 0 2.2 3 5.9 3 5.9s3-3.7 3-5.9c0-1.6-1.2-2.9-3-2.9z" fill="var(--slate-dark)"/><circle cx="8" cy="6.5" r="1.1" fill="#fff"/></svg>
        <span>42 Harbour Lane, Level 6</span>
      </li>
    </ul>
  </article>
</main>
</body>
</html>
```